corvale institute of business and technology web site

I need web site for the institute which focus on business courses and computer course it is also for vocation train for employment It is also carear development and advancement .It should have links to online study resource which free
Industry/Entity Type
Business
Number of Pages Required
1 page
Look and feel
Each slider illustrates characteristics of the customer's brand and the style your logo design should communicate.

```html
<!DOCTYPE html>
<html lang="en">
<head>
<meta charset="utf-8">
<title>Corvale Institute of Business and Technology</title>
<link href="https://fonts.googleapis.com/css2?family=Open+Sans:wght@400;600;700;800&family=Oswald:wght@500;700&display=swap" rel="stylesheet">
<style>
:root{
  --blue:#1b6cb5;
  --navy:#0e3d78;
  --sky:#dcebf8;
  --orange:#f3a01b;
  --green:#7db53a;
  --band:#d5d5d5;
  --ink:#333;
  --muted:#777;
  --footer:#ececec;
  --line:#cfcfcf;
}
*{box-sizing:border-box;margin:0;padding:0}
html,body{width:1200px;height:3016px;overflow:hidden}
body{font-family:"Open Sans",Arial,sans-serif;color:var(--ink);background:#fff;font-size:14px}
.wrap{width:1080px;margin:0 auto;position:relative}

/* header */
.site-header{height:200px;border-bottom:4px solid var(--blue)}
.site-header .wrap{height:100%}
.brand{position:absolute;left:10px;top:22px;display:flex;align-items:center;gap:16px}
.brand-mark{width:84px;height:84px;background:var(--blue);border-radius:6px}
.brand-name{font-weight:800;color:var(--navy);font-size:22px;line-height:1.15;text-transform:uppercase;width:300px}
.topbar{position:absolute;right:0;top:20px;display:flex;align-items:center;gap:26px;font-size:14px;color:var(--navy);font-weight:600}
.topbar .label{font-size:11px;color:var(--blue);display:block;font-weight:700}
.icon{width:28px;height:28px;border-radius:50%;background:var(--blue);display:inline-flex;align-items:center;justify-content:center;vertical-align:middle;margin-right:8px}
.social{display:flex;gap:6px}
.social span{width:24px;height:24px;border-radius:50%;background:var(--navy)}
.search{position:absolute;right:0;top:78px;width:240px;height:30px;border:1px solid var(--line);font-size:12px;color:var(--muted);padding:6px 10px}
.main-nav{position:absolute;right:0;top:140px;display:flex;gap:0}
.main-nav a{display:block;padding:16px 18px;font-size:13px;font-weight:700;color:var(--navy);text-decoration:none}
.main-nav a.active{background:var(--blue);color:#fff}

/* slider */
.slider{height:420px;position:relative;background:linear-gradient(100deg,#9fc9ee 0%,#e9f3fc 45%,#ffffff 60%,#cfe3f6 100%)}
.slider .arrow{position:absolute;top:185px;width:40px;height:50px;background:var(--navy);display:flex;align-items:center;justify-content:center}
.slider .prev{left:0}.slider .next{right:0}

/* welcome */
.welcome{height:260px;text-align:center;padding-top:34px}
.welcome .kicker{color:var(--blue);font-weight:700;font-size:15px}
.welcome h1{color:var(--navy);font-size:28px;font-weight:800;text-transform:uppercase;margin:4px 0 22px}
.welcome p{font-size:13px;line-height:1.65;color:#555;text-align:justify}

/* programs */
.programs{height:530px;background:var(--band);padding-top:0}
.section-tab{display:block;width:300px;margin:0 auto;background:#fff;text-align:center;font-weight:800;color:var(--navy);font-size:17px;padding:12px 0;border-radius:0 0 6px 6px}
.cards{display:flex;gap:20px;margin-top:28px}
.card{flex:1;background:#fff;height:380px;position:relative;padding:12px}
.card h3{font-size:15px;font-weight:700;color:#222;height:44px}
.card .thumb{height:150px;margin-bottom:12px}
.card p{font-size:13px;line-height:1.5;color:#555}
.card .corner{position:absolute;right:0;bottom:0;width:0;height:0;border-left:30px solid transparent;border-bottom:30px solid var(--blue)}
.pager{display:flex;justify-content:center;margin-top:16px}
.pager span{width:44px;height:22px;background:var(--orange);border-radius:11px}

/* study banner */
.study{height:400px;position:relative;background:linear-gradient(180deg,#e9e4da 0%,#f5f2ec 55%,#c9b79a 100%)}
.study .copy{position:absolute;left:60px;top:110px}
.study h2{font-family:"Oswald",sans-serif;font-size:78px;font-weight:700;color:#222;line-height:1}
.study .sub{display:inline-block;background:#2b2b2b;color:#fff;font-family:"Oswald",sans-serif;font-size:30px;font-weight:500;padding:4px 16px;margin-top:6px}
.study .cta{display:block;width:170px;margin-top:14px;background:var(--orange);color:#fff;font-weight:800;font-size:18px;text-align:center;padding:10px 0;border-radius:22px;text-decoration:none}

/* testimonials and form */
.engage{height:790px;padding-top:110px}
.engage .wrap{display:flex;gap:30px}
.left-col{flex:1}
.testimonial{border:1px solid var(--line);height:400px;position:relative;text-align:center}
.testimonial h2{position:absolute;top:-14px;left:50%;transform:translateX(-50%);background:#fff;padding:0 20px;color:var(--navy);font-size:17px;font-weight:800;white-space:nowrap}
.testimonial blockquote{font-style:italic;color:#555;font-size:14px;line-height:1.6;padding:80px 40px 24px}
.person{display:flex;align-items:center;justify-content:center;gap:12px}
.avatar{width:50px;height:50px;border-radius:50%;background:#b8c6d4}
.person strong{display:block;text-align:left;color:var(--navy)}
.person small{color:var(--muted)}
.dots{display:flex;justify-content:center;gap:6px;margin-top:24px}
.dots span{width:9px;height:9px;border-radius:50%;background:#bbb}
.dots span.on{background:var(--blue)}
.alerts{border:1px solid var(--line);margin-top:36px;height:150px;text-align:center;padding-top:26px}
.alerts h2{color:var(--blue);font-weight:800;font-size:20px}
.alerts p{font-size:12px;color:var(--muted);margin:6px 0 12px}
.alerts form{display:flex;justify-content:center}
.alerts .field{width:320px;height:34px;border:1px solid var(--line);font-size:12px;color:var(--muted);padding:8px;text-align:left}
.alerts .btn{background:var(--blue);color:#fff;font-weight:700;font-size:13px;padding:8px 18px}
.question{width:420px;background:var(--blue);height:640px;color:#fff;padding:0 24px;margin-top:-20px}
.question h2{background:var(--navy);margin:0 -24px 24px;padding:20px 0;text-align:center;font-size:19px;font-weight:800}
.question label{display:block;font-size:13px;font-weight:700;margin:10px 0 4px}
.question .field{background:#fff;height:34px;color:var(--muted);font-size:12px;padding:8px}
.question .pair{display:flex;gap:10px}
.question .pair .field{flex:1}
.question .area{height:150px}
.question .submit{margin-top:20px;background:var(--green);text-align:center;font-weight:800;font-size:20px;padding:12px 0}

/* footer */
.site-footer{height:300px;background:var(--footer);padding-top:36px}
.site-footer .wrap{display:flex;gap:30px}
.site-footer .col{flex:1}
.site-footer h4{color:var(--navy);font-size:14px;font-weight:800;margin-bottom:12px}
.site-footer li{list-style:none;font-size:12px;color:#555;line-height:1.9}
.site-footer .news li{line-height:1.4;margin-bottom:10px}
.site-footer .news em{display:block;color:var(--blue);font-style:normal;font-size:11px}
.bottom{height:116px;background:#fff}
.bottom .wrap{display:flex;align-items:center;justify-content:space-between;height:100%}
.partner{display:flex;align-items:center;gap:16px;font-size:12px;font-weight:700;color:#555}
.partner .name{display:flex;align-items:center;gap:10px;background:#1d1d1d;color:#fff;padding:14px 18px;font-size:16px}
.partner .name i{width:18px;height:18px;background:#fff;display:block}
.copyright{font-size:11px;color:var(--muted)}
</style>
</head>
<body>

<header class="site-header">
  <div class="wrap">
    <div class="brand">
      <span class="brand-mark"></span>
      <span class="brand-name">Corvale Institute of Business and Technology</span>
    </div>
    <div class="topbar">
      <div><span class="icon"><svg width="14" height="14" viewBox="0 0 24 24"><path fill="#fff" d="M6.6 10.8a15 15 0 0 0 6.6 6.6l2.2-2.2c.3-.3.7-.4 1-.2 1.1.4 2.3.6 3.6.6.6 0 1 .4 1 1V20c0 .6-.4 1-1 1A17 17 0 0 1 3 4c0-.6.4-1 1-1h3.5c.6 0 1 .4 1 1 0 1.3.2 2.5.6 3.6.1.3 0 .7-.2 1z"/></svg></span><span style="display:inline-block;vertical-align:middle"><span class="label">CALL US</span>+260 211 555 010</span></div>
      <div><span class="icon"><svg width="14" height="14" viewBox="0 0 24 24"><path fill="#fff" d="M3 5h18v14H3z M3 5l9 7 9-7" stroke="#1b6cb5" stroke-width="1.5"/></svg></span><span style="display:inline-block;vertical-align:middle"><span class="label">EMAIL US</span>info@corvaleinstitute.com</span></div>
      <div class="social"><span></span><span></span><span></span><span></span></div>
    </div>
    <div class="search">Search</div>
    <nav class="main-nav">
      <a href="#" class="active">HOME</a><a href="#">ABOUT US</a><a href="#">COURSES</a><a href="#">CONTACT US</a>
    </nav>
  </div>
</header>

<section class="slider" role="img" aria-label="Slide photo of a student working with a glowing digital interface">
  <span class="arrow prev"><svg width="14" height="20"><path d="M11 2 3 10l8 8" stroke="#fff" stroke-width="3" fill="none"/></svg></span>
  <span class="arrow next"><svg width="14" height="20"><path d="M3 2l8 8-8 8" stroke="#fff" stroke-width="3" fill="none"/></svg></span>
</section>

<section class="welcome">
  <div class="wrap">
    <div class="kicker">WELCOME TO</div>
    <h1>Corvale Institute of Business and Technology</h1>
    <p>Corvale Institute of Business and Technology (CIBT) is a fast growing Education &amp; Training Solution Provider, focusing on holistic knowledge and skills transmission that impact livelihoods. It is established on the core values of making a meaningful and measurable difference on career aspirations and goals through innovative learning and knowledge management intervention. CIBT prepares students, not only for professional careers but also inculcates the inquiry mind and discipline in everyone who passes through our doors, mentally, socially and spiritually. The Institution is licensed and registered under the National Vocational Training Authority (NVTA).</p>
  </div>
</section>

<section class="programs">
  <div class="wrap">
    <h2 class="section-tab">PROGRAMS OFFERED</h2>
    <div class="cards">
      <article class="card">
        <h3>University Education – Long Distance Learning</h3>
        <div class="thumb" role="img" aria-label="Photo of a graduate in cap and gown" style="background:linear-gradient(#cdd6df,#8a9bb0)"></div>
        <p>Lorem ipsum dolor sit amet, consectetur adipiscing elit, sed do eiusmod tempor incididunt ut labore et dolore magna aliqua. Ut enim ad minim.</p>
        <span class="corner"></span>
      </article>
      <article class="card">
        <h3>Modular Soft Skills</h3>
        <div class="thumb" role="img" aria-label="Photo of a business workspace" style="background:linear-gradient(#4d7fb8,#1f3f6a)"></div>
        <p>Lorem ipsum dolor sit amet, consectetur adipiscing elit, sed do eiusmod tempor incididunt ut labore et dolore magna aliqua. Ut enim ad minim.</p>
        <span class="corner"></span>
      </article>
      <article class="card">
        <h3>Direct to Device (B2B)</h3>
        <div class="thumb" role="img" aria-label="Photo of app icons on a tablet screen" style="background:linear-gradient(135deg,#3c9be0,#e8632c)"></div>
        <p>Lorem ipsum dolor sit amet, consectetur adipiscing elit, sed do eiusmod tempor incididunt ut labore et dolore magna aliqua. Ut enim ad minim.</p>
        <span class="corner"></span>
      </article>
      <article class="card">
        <h3>Skillmere</h3>
        <div class="thumb" role="img" aria-label="Photo of a professional in an office" style="background:linear-gradient(#e7e7e7,#b7b7b7)"></div>
        <p>Lorem ipsum dolor sit amet, consectetur adipiscing elit, sed do eiusmod tempor incididunt ut labore et dolore magna aliqua. Ut enim ad minim.</p>
        <span class="corner"></span>
      </article>
    </div>
    <div class="pager"><span></span></div>
  </div>
</section>

<section class="study" role="img" aria-label="Photo of a desk with a lamp, laptop and books">
  <div class="copy">
    <h2>ONLINE STUDY</h2>
    <span class="sub">RESOURCE WHICH FREE</span>
    <a class="cta" href="#">CLICK HERE</a>
  </div>
</section>

<section class="engage">
  <div class="wrap">
    <div class="left-col">
      <div class="testimonial">
        <h2>WHAT OUR PEOPLE SAY</h2>
        <blockquote>“Lorem ipsum dolor sit amet, consectetur adipiscing elit, sed do eiusmod tempor incididunt ut labore et dolore magna aliqua. Ut enim ad minim veniam, quis nostrud exercitation ullamco laboris nisi ut aliquip ex ea commodo consequat.”</blockquote>
        <div class="person"><span class="avatar"></span><div><strong>Lena Morrow</strong><small>Lorem ipsum dolor</small></div></div>
        <div class="dots"><span class="on"></span><span></span><span></span></div>
      </div>
      <div class="alerts">
        <h2>AUCTION ALERTS!</h2>
        <p>Sign up to receive email alerts about our upcoming auctions</p>
        <form><div class="field">Enter your email address</div><div class="btn">Subscribe</div></form>
      </div>
    </div>
    <aside class="question">
      <h2>DO YOU HAVE A QUESTION?</h2>
      <label>Your Name*</label>
      <div class="pair"><div class="field">First Name</div><div class="field">Last Name</div></div>
      <label>Email*</label>
      <div class="field">Your Email Address Here</div>
      <label>Phone</label>
      <div class="field">Phone Number</div>
      <label>Comments*</label>
      <div class="field area"></div>
      <div class="submit">SUBMIT</div>
    </aside>
  </div>
</section>

<footer class="site-footer">
  <div class="wrap">
    <div class="col"><h4>NAVIGATION</h4><ul><li>Home</li><li>About Us</li><li>Courses</li><li>Contact Us</li></ul></div>
    <div class="col"><h4>PROGRAMS OFFERED</h4><ul><li>University Education – Long Distance Learning</li><li>Modular Soft Skills</li><li>Direct To Device (B2B)</li><li>Skillmere</li><li>Skillmere Roles In The Talent Continuum</li><li>Business Verticals</li><li>Technology Capabilities</li></ul></div>
    <div class="col news"><h4>RECENT NEWS</h4><ul><li><em>January 18, 2015</em>Lorem ipsum dolor sit amet, consec tetur adipiscing elit</li><li><em>January 18, 2015</em>Lorem ipsum dolor sit amet, consec tetur adipiscing elit</li><li><em>January 18, 2015</em>Lorem ipsum dolor sit amet, consec tetur adipiscing elit</li></ul></div>
    <div class="col"><h4>CONTACT INFO</h4><ul><li>Plot 14 Meridian Road, Lusaka</li><li>Phone: +260 211 555 010</li><li>Mobile: +260 970 555 020</li><li>info@corvaleinstitute.com</li></ul></div>
  </div>
</footer>

<div class="bottom">
  <div class="wrap">
    <div class="partner">IN CONJUNCTION<br>WITH SKILLMERE <span class="name"><i></i>SKILLMERE</span></div>
    <div class="copyright">© 2015 Corvale Institute of Business and Technology. All Rights Reserved.</div>
  </div>
</div>

</body>
</html>
```